Thornvale Group needs a business card design

We need a new business card design using the logo recently selected in a logo competition on Pixel Bazaar. Our business is a consultancy specializing in aviation and energy and the winning business card design will promote an image of precision and professionalism with creativity.

Please use the logo with the name on the front of the card and use a complementary font. Make the back white with either the light grey or dark grey logo.

Target Market(s)

Senior finance and legal leaders at aviation and energy companies

Industry/Entity Type

Management Consulting

Contact Information for Business Card

Peter Castrell
President
Thornvale Group

www.thornvalegroup.example

(555) 204-6391
pc@thornvalegroup.example

Requirements
Must have
• Professional font that goes well with the logo font

```html
<!DOCTYPE html>
<html lang="en">
<head>
<meta charset="utf-8">
<title>Thornvale Group — Business Card</title>
<link href="https://fonts.googleapis.com/css2?family=Source+Sans+3:wght@400;600;700&display=swap" rel="stylesheet">
<style>
  :root {
    --stage: #000000;
    --card-top: #dedede;
    --card-bottom: #e9e9e9;
    --navy: #1b3f6e;
    --rule: #6f8fb8;
    --ink-grey: #555555;
    --divider: #c9c9c9;
  }
  * { margin: 0; padding: 0; box-sizing: border-box; }
  html, body {
    width: 1200px; height: 900px; overflow: hidden;
    background: var(--stage);
    font-family: "Source Sans 3", "Helvetica Neue", Arial, sans-serif;
  }
  .canvas { position: relative; width: 1200px; height: 900px; }
  .card {
    position: absolute; top: 271px;
    width: 457px; height: 281px;
    border-radius: 14px;
    background: linear-gradient(180deg, var(--card-top), var(--card-bottom));
    overflow: hidden;
  }
  .card--front { left: 137px; }
  .card--back { left: 626px; }

  .brand-name {
    position: absolute;
    color: var(--navy);
    font-weight: 600;
    white-space: nowrap;
  }
  .card--front .brand-name {
    left: 32px; top: 92px;
    font-size: 23px;
    display: flex; align-items: center; gap: 9px;
  }
  .brand-mark { width: 12px; height: 12px; background: var(--navy); display: inline-block; }

  .card--back .brand-name {
    left: 0; right: 0; top: 150px;
    text-align: center;
    font-size: 36px;
    letter-spacing: 1px;
  }

  .v-divider {
    position: absolute; left: 229px; top: 55px;
    width: 1px; height: 144px; background: var(--divider);
  }
  .person { position: absolute; left: 249px; top: 78px; }
  .person__name { color: var(--navy); font-weight: 700; font-size: 18px; line-height: 22px; }
  .person__title { color: var(--ink-grey); font-size: 13px; line-height: 14px; }

  .contact { position: absolute; left: 249px; top: 144px; list-style: none; }
  .contact li {
    display: flex; align-items: center; gap: 8px;
    color: var(--ink-grey); font-size: 13px; line-height: 20px;
  }
  .contact svg { width: 10px; height: 10px; fill: var(--navy); }

  .tagline {
    position: absolute; left: 0; right: 0; top: 212px;
    display: flex; align-items: center; gap: 9px;
    color: var(--navy); font-weight: 600; font-size: 16px;
  }
  .tagline::before, .tagline::after {
    content: ""; height: 1px; background: var(--rule);
  }
  .tagline::before { width: 88px; }
  .tagline::after { flex: 1; }

  .sectors {
    position: absolute; left: 0; right: 0; top: 241px;
    text-align: center; color: var(--ink-grey);
    font-weight: 600; font-size: 13px;
    padding-right: 28px;
  }
  .sectors .sep { color: var(--navy); margin: 0 3px; }
</style>
</head>
<body>
<main class="canvas">
  <section class="card card--front" aria-label="Card front">
    <div class="brand-name"><span class="brand-mark"></span>Thornvale Group</div>
    <div class="v-divider"></div>
    <div class="person">
      <p class="person__name">Peter J. Castrell</p>
      <p class="person__title">President</p>
    </div>
    <ul class="contact">
      <li>
        <svg viewBox="0 0 24 24" aria-hidden="true"><path d="M6.6 10.8a15 15 0 0 0 6.6 6.6l2.2-2.2a1 1 0 0 1 1-.25 11.4 11.4 0 0 0 3.6.6 1 1 0 0 1 1 1V20a1 1 0 0 1-1 1A17 17 0 0 1 3 4a1 1 0 0 1 1-1h3.5a1 1 0 0 1 1 1c0 1.25.2 2.45.6 3.6a1 1 0 0 1-.25 1z"/></svg>
        (555) 204-6391
      </li>
      <li>
        <svg viewBox="0 0 24 24" aria-hidden="true"><path d="M2 5h20v14H2z M2 5l10 7 10-7" /><path d="M3 6.5l9 6.3 9-6.3V18H3z" fill="#e4e4e4"/></svg>
        pc@thornvalegroup.example
      </li>
    </ul>
    <p class="tagline">Finance and Strategy Consulting</p>
    <p class="sectors">Aviation<span class="sep">&lsaquo;</span> Manufacturing<span class="sep">&lsaquo;</span> Energy</p>
  </section>

  <section class="card card--back" aria-label="Card back">
    <div class="brand-name">Thornvale Group</div>
  </section>
</main>
</body>
</html>
```